Carrying bags for customer visit

I am looking to make a carrying case that can be used to carry small presents, gifts, our brochure (20 inch X20 inch) and sometimes our samples (which are printed circuit boards that have a size of 24X15). The case should look elegant, show our company logo and our slogan "PCB is our business". You can try to download our logo from our web site www.tvolamiq.com. I want a contemporary and cool feel of the carrying case that can be any materials. I prefer to use recyclable materials that reflects our company's business philosophy of practicing sustanbility. Also I would like to add Chinese name “泓岚科技(东莞)有限公司" in the bag.

Target Market(s)

Corporate customers who will come into contact with our companies

Colors

Designer to choose colors to be used in the design.

Requirements
Must have
• It has to be attractive and people wanting to use them on a regular basis. Therefore, the logo display and our slogan should be subtle. I want the carrying bags not to be very expensive to produce.

```html
<!DOCTYPE html>
<html lang="en">
<head>
<meta charset="utf-8">
<title>Tvolamiq Carrying Bag</title>
<link href="https://fonts.googleapis.com/css2?family=Montserrat:wght@400;700;800&family=Noto+Sans+SC:wght@400&display=swap" rel="stylesheet">
<style>
  :root {
    --bg: #e9e9e9;
    --paper: #ffffff;
    --paper-shade: #f2f2f2;
    --brand-green: #0f5a28;
    --circuit-grey: #8a8a8a;
    --ink: #2b2b2b;
    --ornament: #b9b9b9;
  }
  html, body {
    margin: 0;
    padding: 0;
    width: 1200px;
    height: 1200px;
    overflow: hidden;
    background: var(--bg);
  }
  .bag-face {
    position: absolute;
    left: 250px;
    top: 70px;
    width: 700px;
    height: 1060px;
    display: block;
  }
  .brand-name {
    font-family: 'Montserrat', sans-serif;
    font-weight: 800;
    font-size: 74px;
    fill: var(--brand-green);
    letter-spacing: 2px;
  }
  .slogan {
    font-family: 'Montserrat', sans-serif;
    font-size: 37px;
    fill: var(--ink);
  }
  .slogan-strong {
    font-weight: 700;
    fill: var(--brand-green);
  }
  .company-cn {
    font-family: 'Noto Sans SC', sans-serif;
    font-size: 25px;
    fill: #ffffff;
  }
</style>
</head>
<body>
<svg class="bag-face" viewBox="0 0 700 1060" xmlns="http://www.w3.org/2000/svg">
  <defs>
    <linearGradient id="paperGradient" x1="0" y1="0" x2="1" y2="1">
      <stop offset="0" stop-color="var(--paper)"/>
      <stop offset="1" stop-color="var(--paper-shade)"/>
    </linearGradient>
  </defs>

  <!-- paper panel -->
  <rect class="panel" x="0" y="0" width="700" height="1060" fill="url(#paperGradient)"/>

  <!-- corner ornaments -->
  <rect class="corner-ornament" role="img" aria-label="Filigree corner ornament" x="20" y="40" width="150" height="80" fill="var(--ornament)" opacity="0.35"/>
  <rect class="corner-ornament" role="img" aria-label="Filigree corner ornament" x="530" y="40" width="150" height="80" fill="var(--ornament)" opacity="0.35"/>

  <!-- frame side lines -->
  <line class="frame-line" x1="28" y1="120" x2="28" y2="620" stroke="var(--ink)" stroke-width="1.5"/>
  <line class="frame-line" x1="672" y1="120" x2="672" y2="620" stroke="var(--ink)" stroke-width="1.5"/>

  <!-- brand name -->
  <text class="brand-name" x="350" y="575" text-anchor="middle">TVOLAMIQ</text>

  <!-- rule and slogan -->
  <line class="slogan-rule" x1="152" y1="630" x2="548" y2="630" stroke="var(--brand-green)" stroke-width="2"/>
  <text class="slogan" x="350" y="678" text-anchor="middle">PCB IS OUR <tspan class="slogan-strong">BUSINESS</tspan></text>

  <!-- green band and swoosh -->
  <rect class="green-band" x="0" y="752" width="700" height="50" fill="var(--brand-green)"/>
  <path class="white-swoosh" d="M0 770 Q200 772 390 752 Q540 772 700 772 L700 790 Q540 792 390 770 Q200 795 0 792 Z" fill="var(--paper)"/>

  <!-- circuit texture base -->
  <path class="circuit-field" role="img" aria-label="Circuit board trace pattern"
        d="M0 800 Q200 798 390 778 Q540 798 700 798 L700 1060 L0 1060 Z" fill="var(--circuit-grey)"/>

  <!-- Chinese company name pill -->
  <rect class="company-pill" x="187" y="955" width="380" height="50" rx="8" fill="var(--brand-green)"/>
  <text class="company-cn" x="377" y="989" text-anchor="middle">泓岚科技(东莞)有限公司</text>
</svg>
</body>
</html>
```